Psychiatric Office Needs a Website- 1st Time Ever!

Been in practice since 2003 with no website, but finally ready to dive in. We are Maplecrest Behavioral Healthcare, a mental health outpatient practice based in Fayetteville, Georgia that sees diverse individuals and families from childhood to advanced age for a variety of conditions. We've grown by word of mouth and referral but would now like to have a digital footprint. Be the pioneer of our website and we will be sure to share. We would like to see designs that are modern, animated, fairly colorful, easy to read, and caters to all ages. Also, we would like the design to take the whole page (not be centered) and can be viewed well on phone/tablet. Please see our outline for more information. Our motto/slogan is: Maplecrest Behavioral Healthcare- A step forward in your wellness journey, so the design should try to reflect that.
Updates

Project Deadline Extended
Reason: site in progress

Target Market(s)

Children through elderly

Industry/Entity Type

Medical

Logo Text

Stepping forward in your wellness journey

Number of Pages Required

1 page

Colors

Designer to choose colors to be used in the design.

Requirements
Must have
• Animation or moving pictures.
• Color.
• Concise.
• User friendly
• Diversity in the stock photos

```html
<!DOCTYPE html>
<html lang="en">
<head>
<meta charset="utf-8">
<title>Maplecrest Behavioral Healthcare</title>
<link href="https://fonts.googleapis.com/css2?family=Open+Sans:wght@400;600;700&family=Lobster&display=swap" rel="stylesheet">
<style>
:root{
  --blue:#2a8fd0;
  --blue-dark:#1f74ad;
  --green:#74b843;
  --green-dark:#5a9a2e;
  --ink:#333a40;
  --muted:#7a8288;
  --light:#f3f4f5;
  --line:#dfe3e6;
  --footer:#2d3033;
  --footer-deep:#232527;
  --white:#ffffff;
}
*{box-sizing:border-box;margin:0;padding:0}
html,body{width:1200px;height:4336px;overflow:hidden}
body{font-family:"Open Sans",Arial,sans-serif;color:var(--ink);background:var(--white);font-size:14px;position:relative}
.script{font-family:"Lobster",cursive;font-weight:400}
a{color:inherit;text-decoration:none}
.btn{display:inline-block;background:var(--green);color:var(--white);font-weight:700;font-size:13px;letter-spacing:.5px;padding:12px 30px;border-radius:24px;text-transform:uppercase}

/* header */
.site-header{position:absolute;top:0;left:0;width:1200px;height:180px}
.topbar{position:absolute;right:0;top:0;width:560px;height:36px;background:var(--blue);color:var(--white);font-size:12px;font-weight:600;display:flex;align-items:center;padding-left:230px;letter-spacing:.3px}
.topbar svg{margin-right:8px}
.header-contact{position:absolute;right:100px;top:52px;display:flex;align-items:center;gap:22px}
.header-phone{color:var(--green);font-weight:700;font-size:14px;display:flex;align-items:center;gap:8px}
.header-phone span{color:var(--ink)}
.portal{background:var(--green);color:var(--white);font-weight:700;font-size:12px;padding:10px 26px;border-radius:4px}
.brand{position:absolute;left:100px;top:18px;display:flex;align-items:center;gap:14px}
.brand-mark{width:54px;height:54px;border-radius:50%;background:var(--green)}
.brand-name{font-size:19px;font-weight:700;color:var(--blue);line-height:1.2;width:180px}
.main-nav{position:absolute;right:100px;top:138px;display:flex;gap:34px;font-size:12px;font-weight:600;color:var(--ink)}
.main-nav a:first-child{color:var(--blue)}

/* hero */
.hero{position:absolute;top:180px;left:0;width:1200px;height:600px;overflow:hidden}
.hero-photo{position:absolute;inset:0;background:linear-gradient(100deg,#6f8a54 0%,#a9b98a 35%,#d9dcc4 60%,#b7c7d6 100%)}
.hero-text{position:absolute;left:130px;top:200px;color:var(--white)}
.hero-text h1{font-family:"Lobster",cursive;font-weight:400;font-size:44px;line-height:1.1}
.hero-text p{font-size:17px;margin:10px 0 30px}
.hero-arrow{position:absolute;top:270px;width:34px;height:50px;background:rgba(255,255,255,.25);display:flex;align-items:center;justify-content:center}
.hero-arrow.left{left:0}.hero-arrow.right{right:0}
.hero-wave{position:absolute;left:0;bottom:0}

/* about */
.about{position:absolute;top:820px;left:0;width:1200px;height:460px}
.about-copy{position:absolute;left:100px;top:20px;width:560px}
.about-copy h2{font-size:34px;font-weight:700;color:var(--ink)}
.about-copy h3{font-family:"Lobster",cursive;font-weight:400;font-size:28px;color:var(--blue);margin-bottom:18px}
.about-copy p{font-size:13px;line-height:1.75;color:var(--muted);margin-bottom:12px}
.about-copy .btn{margin-top:14px}
.appointment{position:absolute;left:720px;top:20px;width:380px;background:var(--white);border:1px solid var(--line);box-shadow:0 2px 10px rgba(0,0,0,.07);padding:22px 26px 26px}
.appointment h4{font-size:20px;font-weight:600;letter-spacing:1px;text-align:center;color:var(--ink);padding-bottom:12px;border-bottom:2px solid var(--line);margin-bottom:16px}
.field{border:1px solid var(--line);height:34px;font-size:11px;color:#9aa;padding:9px 10px;margin-bottom:10px}
.field-row{display:flex;gap:10px}.field-row .field{flex:1}
.field.tall{height:60px}
.submit{background:var(--blue);color:var(--white);text-align:center;font-weight:700;font-size:13px;padding:11px;margin-top:4px}

/* services */
.services{position:absolute;top:1320px;left:0;width:1200px;height:900px;background:var(--light)}
.section-title{text-align:center;font-family:"Lobster",cursive;font-weight:400;font-size:42px;color:var(--ink)}
.section-title em{font-style:normal;color:var(--blue)}
.services .section-title{padding-top:68px}
.title-rule{width:60px;height:3px;background:var(--green);margin:10px auto 0}
.service-grid{position:absolute;left:100px;top:160px;width:1000px;display:grid;grid-template-columns:repeat(3,316px);column-gap:26px;row-gap:40px}
.service-card{background:var(--white);box-shadow:0 2px 8px rgba(0,0,0,.06)}
.service-photo{height:180px}
.service-card h5{height:80px;display:flex;align-items:center;justify-content:center;text-align:center;font-size:13px;font-weight:700;line-height:1.45;padding:0 20px}
.service-card h5 small{font-size:10px;font-weight:400}
.services .btn{position:absolute;left:528px;top:805px;padding:12px 36px}

/* conditions */
.conditions{position:absolute;top:2260px;left:0;width:1200px;height:460px}
.conditions .section-title{padding-top:70px}
.condition-list{position:absolute;top:190px;left:100px;width:1000px;display:flex;justify-content:space-between;align-items:flex-start}
.condition{width:180px;text-align:center;font-size:13px;color:var(--ink)}
.condition-ring{width:124px;height:124px;border-radius:50%;border:3px solid var(--green);margin:18px auto 14px;display:flex;align-items:center;justify-content:center}
.condition-ring .dot{width:82px;height:82px;border-radius:50%;background:linear-gradient(135deg,#8cc85a,#5a9a2e)}
.condition.featured .condition-ring{width:160px;height:160px;margin-top:0}
.condition.featured .dot{width:110px;height:110px}

/* faq */
.faq{position:absolute;top:2720px;left:0;width:1200px;height:440px;overflow:hidden}
.faq-photo{position:absolute;left:0;top:0;width:700px;height:440px;background:linear-gradient(120deg,#c8d7e2,#e8eef2 50%,#9fb6c7)}
.faq-panel{position:absolute;right:0;top:0;width:640px;height:440px;background:var(--blue);clip-path:polygon(18% 0,100% 0,100% 100%,0 100%)}
.faq-content{position:absolute;left:670px;top:38px;width:460px}
.faq-content h2{font-family:"Lobster",cursive;font-weight:400;color:var(--white);font-size:30px;margin-bottom:18px}
.faq-item{height:30px;background:var(--green);color:var(--white);font-size:11px;font-weight:600;display:flex;align-items:center;justify-content:space-between;padding:0 12px;margin-bottom:6px}
.faq-item.open{background:var(--white);color:var(--ink);font-weight:400}
.faq-more{color:var(--white);font-size:12px;text-align:right;margin-top:10px}

/* news */
.news{position:absolute;top:3200px;left:0;width:1200px;height:560px}
.news .section-title{padding-top:30px}
.news-grid{position:absolute;left:100px;top:128px;width:1000px;display:grid;grid-template-columns:repeat(3,316px);column-gap:26px}
.news-card{background:var(--white);box-shadow:0 2px 8px rgba(0,0,0,.08);text-align:center}
.news-photo{height:200px}
.news-card h5{font-size:12px;font-weight:700;margin:20px 0 10px;letter-spacing:.3px}
.news-card p{font-size:11px;color:var(--muted);line-height:1.6;padding:0 26px}
.news-meta{font-size:10px;color:var(--green);padding:14px 0 18px;display:flex;justify-content:center;gap:18px}

/* footer */
.site-footer{position:absolute;top:3780px;left:0;width:1200px;height:556px;color:#c9cdd0}
.footer-wave{position:absolute;top:0;left:0}
.footer-body{position:absolute;top:90px;left:0;width:1200px;height:466px;background:var(--footer)}
.footer-cols{position:absolute;left:100px;top:70px;width:1000px;display:grid;grid-template-columns:300px 220px 300px 180px}
.footer-cols h6{color:var(--white);font-size:14px;font-weight:700;letter-spacing:.5px;margin-bottom:22px}
.contact-line{display:flex;gap:12px;font-size:12px;line-height:1.6;margin-bottom:16px}
.contact-line svg{flex:none;margin-top:3px}
.quick-links li{list-style:none;font-size:12px;margin-bottom:10px;padding-left:14px;position:relative}
.quick-links li::before{content:"";position:absolute;left:0;top:6px;width:5px;height:5px;background:var(--green);border-radius:50%}
.newsletter p{font-size:12px;line-height:1.6;margin-bottom:14px}
.newsletter .input{height:34px;background:var(--white);color:#999;font-size:11px;padding:9px 10px;width:240px;margin-bottom:10px}
.newsletter .btn{padding:9px 22px;font-size:11px;border-radius:3px}
.social{display:flex;gap:10px;align-items:center;font-size:12px}
.social span.circle{width:36px;height:36px;border-radius:50%;border:2px solid #8a9095}
.copyright{position:absolute;left:0;bottom:0;width:1200px;height:56px;background:var(--footer-deep);font-size:11px;color:#9aa0a5;display:flex;align-items:center;justify-content:center;border-top:1px solid #3a3e41}
</style>
</head>
<body>

<header class="site-header">
  <div class="topbar">
    <svg width="14" height="14" viewBox="0 0 14 14"><circle cx="7" cy="7" r="6" fill="none" stroke="#fff" stroke-width="1.5"/><path d="M7 3.5V7l2.5 1.5" stroke="#fff" stroke-width="1.5" fill="none"/></svg>
    OPENING HOURS : MON - SAT : 8.30 - 18.00
  </div>
  <div class="brand">
    <span class="brand-mark"></span>
    <span class="brand-name">Maplecrest Behavioral Healthcare</span>
  </div>
  <div class="header-contact">
    <div class="header-phone">
      <svg width="16" height="16" viewBox="0 0 16 16"><path d="M4 1.5l2.5 3-1.5 2a9 9 0 0 0 4.5 4.5l2-1.5 3 2.5-1.5 2.5C7 14.5 1.5 9 1.5 3z" fill="#74b843"/></svg>
      PHONE: <span>(555) 014-2297</span>
    </div>
    <a class="portal" href="#">PATIENT PORTAL</a>
  </div>
  <nav class="main-nav">
    <a href="#">HOME</a><a href="#">ABOUT US</a><a href="#">SERVICES</a><a href="#">CONDITIONS WE TREAT</a><a href="#">NEW PATIENTS</a><a href="#">CONTACT US</a>
  </nav>
</header>

<section class="hero">
  <div class="hero-photo" role="img" aria-label="Photograph of a smiling grandfather carrying a young child on his shoulders outdoors"></div>
  <div class="hero-arrow left"><svg width="12" height="20" viewBox="0 0 12 20"><path d="M10 2L2 10l8 8" stroke="#fff" stroke-width="2.5" fill="none"/></svg></div>
  <div class="hero-arrow right"><svg width="12" height="20" viewBox="0 0 12 20"><path d="M2 2l8 8-8 8" stroke="#fff" stroke-width="2.5" fill="none"/></svg></div>
  <div class="hero-text">
    <h1>Maplecrest Behavioral Healthcare</h1>
    <p>A step forward in your wellness journey</p>
    <a class="btn" href="#">Take a Screening</a>
  </div>
  <svg class="hero-wave" width="1200" height="90" viewBox="0 0 1200 90">
    <path d="M0 40 C300 95 700 0 1200 50 L1200 90 L0 90Z" fill="#74b843"/>
    <path d="M0 55 C320 105 720 15 1200 62 L1200 90 L0 90Z" fill="#2a8fd0"/>
    <path d="M0 66 C330 112 730 28 1200 72 L1200 90 L0 90Z" fill="#fff"/>
  </svg>
</section>

<section class="about">
  <div class="about-copy">
    <h2>About</h2>
    <h3>Maplecrest Behavioral Healthcare</h3>
    <p>For more than twenty years our outpatient practice has cared for children, teens, adults and older adults across our community, working together to promote lasting mental wellness for every family.</p>
    <p>We provide mental health services to children, adults and the developmentally disabled, with a culturally sensitive approach regardless of age, race, gender, orientation or religion. Our caring team works with each client to overcome mental health challenges and improve quality of life, setting personal treatment goals with patients and caregivers alike.</p>
    <a class="btn" href="#">Read More</a>
  </div>
  <form class="appointment">
    <h4>APPOINTMENT FORM</h4>
    <div class="field">Your Name</div>
    <div class="field-row"><div class="field">Email</div><div class="field">Phone</div></div>
    <div class="field-row"><div class="field">Date</div><div class="field">Time</div></div>
    <div class="field tall">Your Message</div>
    <div class="submit">SUBMIT</div>
  </form>
</section>

<section class="services">
  <h2 class="section-title">Our <em>Services</em></h2>
  <div class="title-rule"></div>
  <div class="service-grid">
    <div class="service-card"><div class="service-photo" role="img" aria-label="Photo of a doctor reviewing results with a patient" style="background:linear-gradient(135deg,#cfd9e0,#eef1f3)"></div><h5>DIAGNOSTIC EVALUATION AND TREATMENT</h5></div>
    <div class="service-card"><div class="service-photo" role="img" aria-label="Photo of a therapist in session with a client" style="background:linear-gradient(135deg,#d6c8b6,#f0e8dc)"></div><h5>PSYCHOPHARMACOLOGY</h5></div>
    <div class="service-card"><div class="service-photo" role="img" aria-label="Photo of a measuring tape around a waist" style="background:linear-gradient(135deg,#e6b8a0,#f5ddd0)"></div><h5>BARIATRIC PRE-SURGICAL CONSULTATION <small>(and other surgeries)</small></h5></div>
    <div class="service-card"><div class="service-photo" role="img" aria-label="Photo of a diverse family smiling together" style="background:linear-gradient(135deg,#b7c9a8,#e4ecd8)"></div><h5>DISABILITY AND<br>WORK RELATED REPORTS <small>(mental)</small></h5></div>
    <div class="service-card"><div class="service-photo" role="img" aria-label="Photo of a child at an early childhood assessment" style="background:linear-gradient(135deg,#bcd3e6,#e6eef6)"></div><h5>EARLY CHILDHOOD ASSESSMENTS</h5></div>
    <div class="service-card"><div class="service-photo" role="img" aria-label="Photo of a counselor supporting a young adult" style="background:linear-gradient(135deg,#c9b8a8,#ece2d6)"></div><h5>SUBSTANCE ABUSE ASSESSMENTS</h5></div>
  </div>
  <a class="btn" href="#">View All Services</a>
</section>

<section class="conditions">
  <h2 class="section-title">Conditions <em>We Treat</em></h2>
  <div class="title-rule"></div>
  <div class="condition-list">
    <div class="condition"><div class="condition-ring"><span class="dot" role="img" aria-label="Icon for mood disorders"></span></div>Mood Disorders</div>
    <div class="condition"><div class="condition-ring"><span class="dot" role="img" aria-label="Icon for anxiety disorders"></span></div>Anxiety Disorders</div>
    <div class="condition featured"><div class="condition-ring"><span class="dot" role="img" aria-label="Icon for childhood disorders"></span></div>Common Disorders of<br>Childhood</div>
    <div class="condition"><div class="condition-ring"><span class="dot" role="img" aria-label="Icon for psychotic disorders"></span></div>Psychotic Disorders</div>
    <div class="condition"><div class="condition-ring"><span class="dot" role="img" aria-label="Icon for eating disorders"></span></div>Eating Disorders</div>
  </div>
</section>

<section class="faq">
  <div class="faq-photo" role="img" aria-label="Photo of a stethoscope and a clinician writing on a tablet"></div>
  <div class="faq-panel"></div>
  <div class="faq-content">
    <h2>Frequently Asked Questions</h2>
    <div class="faq-item"><span>What do I need to bring with me to my first visit?</span><span>−</span></div>
    <div class="faq-item open"><span>Insurance card, photo ID and the forms found on our Patients page.</span></div>
    <div class="faq-item"><span>How long do I have to wait to be seen?</span><span>+</span></div>
    <div class="faq-item"><span>What types of insurance do you accept?</span><span>+</span></div>
    <div class="faq-item"><span>Why is my child not doing well in school?</span><span>+</span></div>
    <div class="faq-item"><span>I feel sad and tired. Do I still have energy to help myself?</span><span>+</span></div>
    <div class="faq-more">View All »</div>
  </div>
</section>

<section class="news">
  <h2 class="section-title">Latest <em>News &amp; Tips</em></h2>
  <div class="title-rule"></div>
  <div class="news-grid">
    <article class="news-card"><div class="news-photo" role="img" aria-label="Photo of a person sitting alone in thought" style="background:linear-gradient(135deg,#9ea7ad,#d5dadd)"></div><h5>CIRCUMSTANCES OCCUR PAULA</h5><p>Simple steps to ease everyday stress and build calm habits for the whole family.</p><div class="news-meta"><span>March 15,2017</span><span>No comments</span><span>Like</span></div></article>
    <article class="news-card"><div class="news-photo" role="img" aria-label="Photo of a nurse talking with a patient" style="background:linear-gradient(135deg,#a8c4d8,#e1ebf2)"></div><h5>SED QUIA NON NUMQUAM EIUS</h5><p>How regular check-ins help children and teens share their feelings openly.</p><div class="news-meta"><span>March 15,2017</span><span>No comments</span><span>Like</span></div></article>
    <article class="news-card"><div class="news-photo" role="img" aria-label="Photo of a counselor meeting with a client" style="background:linear-gradient(135deg,#b9c4b0,#e3e8dc)"></div><h5>QUIS NOSTRUD EXERCITATIO</h5><p>Tips for older adults on staying connected, active and well through each season.</p><div class="news-meta"><span>March 15,2017</span><span>No comments</span><span>Like</span></div></article>
  </div>
</section>

<footer class="site-footer">
  <svg class="footer-wave" width="1200" height="100" viewBox="0 0 1200 100">
    <path d="M0 30 C350 90 800 -10 1200 40 L1200 100 L0 100Z" fill="#74b843"/>
    <path d="M0 48 C360 105 810 10 1200 58 L1200 100 L0 100Z" fill="#2a8fd0"/>
    <path d="M0 62 C370 115 820 25 1200 72 L1200 100 L0 100Z" fill="#2d3033"/>
  </svg>
  <div class="footer-body">
    <div class="footer-cols">
      <div>
        <h6>CONTACT US</h6>
        <div class="contact-line"><svg width="12" height="16" viewBox="0 0 12 16"><path d="M6 1a5 5 0 0 1 5 5c0 4-5 9-5 9S1 10 1 6a5 5 0 0 1 5-5z" fill="#74b843"/><circle cx="6" cy="6" r="2" fill="#2d3033"/></svg><span>212 Peachtree Commons Way,<br>Fayetteville, Georgia</span></div>
        <div class="contact-line"><svg width="14" height="14" viewBox="0 0 16 16"><path d="M4 1.5l2.5 3-1.5 2a9 9 0 0 0 4.5 4.5l2-1.5 3 2.5-1.5 2.5C7 14.5 1.5 9 1.5 3z" fill="#74b843"/></svg><span>Call Us : (555) 014-2297</span></div>
        <div class="contact-line"><svg width="14" height="14" viewBox="0 0 14 14"><circle cx="7" cy="7" r="6" fill="none" stroke="#74b843" stroke-width="1.5"/><path d="M7 3.5V7l2.5 1.5" stroke="#74b843" stroke-width="1.5" fill="none"/></svg><span>Hours : Mon-Sat : 8.30 to 18.00</span></div>
        <div class="contact-line"><svg width="14" height="12" viewBox="0 0 14 12"><rect x="1" y="1" width="12" height="10" fill="none" stroke="#74b843" stroke-width="1.5"/><path d="M1 1l6 5 6-5" stroke="#74b843" stroke-width="1.5" fill="none"/></svg><span>info@maplecrestbh.example</span></div>
      </div>
      <div>
        <h6>QUICK LINKS</h6>
        <ul class="quick-links"><li>Home</li><li>About Us</li><li>Services</li><li>Conditions We Treat</li><li>New Patients</li><li>Contact Us</li></ul>
      </div>
      <div class="newsletter">
        <h6>SIGN UP NEWSLETTER</h6>
        <p>Get helpful wellness news, tips and updates delivered to your inbox.</p>
        <div class="input">Email Address</div>
        <a class="btn" href="#">Subscribe</a>
      </div>
      <div>
        <h6>FOLLOW US</h6>
        <div class="social"><span class="circle"></span><span>Follow Us</span></div>
      </div>
    </div>
    <div class="copyright">© Copyright 2017 : Maplecrest Behavioral Healthcare : All rights reserved | Privacy policy</div>
  </div>
</footer>

</body>
</html>
```